New Website Design for PHOVAN.org

We are looking for a new website design for PHOVAN.org. PHOVAN is a non profit home inspector association based in California. Home Inspectors are people that come out and look at a house before it's purchased to let the buyer know of any defects that may exist.
Our site is based on Joomla so if you'll be able to make a Joomla 3 template as well, please let us know (not required, but a bonus).
We would like to see designs that incorporate royal blue, white and chrome into the site as that's our main business colors.
We would like a place for rotating banners though they don't need to be the same size as the current site.
We would like navigation to be easier to manage with menus only across the top (via drop down menus) where we are going to sort out the items currently on the side. Possibly the front page could have a graphic link to separate portals for Realtors, Home Buyers and Inspectors, but that's just one option.
We would like a good mobile design or something that will scale easily to mobile.
The Find an Inspector feature is important and should stand out. The ASK PHOVANr site
Current home page feels a bit busy. Would like to simplify a bit.

```html
<!DOCTYPE html>
<html lang="en">
<head>
<meta charset="utf-8">
<title>PHOVAN.org</title>
<link href="https://fonts.googleapis.com/css2?family=Montserrat:wght@400;500;600&family=Open+Sans:wght@400;600;700&display=swap" rel="stylesheet">
<style>
:root{
  --royal:#243a94;
  --royal-dark:#1c2f7e;
  --ink:#333;
  --muted:#8a8a8a;
  --page:#f9f9f9;
  --footer:#242424;
  --footer-line:#3a3a3a;
  --white:#fff;
}
*{margin:0;padding:0;box-sizing:border-box}
html,body{width:969px;height:1200px;overflow:hidden}
body{position:relative;background:linear-gradient(#e9e6e2,#d8d8dc 60%,#dcdde0);font-family:"Open Sans",Arial,sans-serif;color:var(--ink)}
.side-scene{position:absolute;top:0;height:700px;width:120px;background:linear-gradient(90deg,#c9a77a,#e6d3b3 40%,#a9c3dd 70%,#d7c09a)}
.side-scene.left{left:0}
.side-scene.right{right:0;width:111px;background:linear-gradient(90deg,#d7c09a,#a9c3dd 35%,#e6d3b3 70%,#c9a77a)}
.top-rule{position:absolute;top:0;left:0;width:969px;height:3px;background:var(--royal)}
.sheet{position:absolute;left:120px;top:3px;width:738px;height:905px;background:var(--page)}
.social{position:absolute;top:49px;display:flex;gap:6px;left:161px}
.social span{width:22px;height:22px;border-radius:50%;background:#c4c4c4;display:block}
.brand{position:absolute;left:437px;top:12px;width:104px;height:104px;border-radius:50%;border:3px solid var(--royal);background:var(--white);display:flex;align-items:center;justify-content:center;font:700 17px "Open Sans",sans-serif;color:var(--royal)}
.contact{position:absolute;left:691px;top:40px;font:500 11.5px "Montserrat",sans-serif;color:var(--royal);line-height:13px}
.contact .lab{display:inline-block;width:46px}
.contact a{color:var(--royal)}
.nav{position:absolute;top:120px;left:162px;display:flex;align-items:center;font:500 10px "Montserrat",sans-serif;color:#444;text-transform:uppercase}
.nav li{list-style:none;margin-right:20px}
.nav .current{background:var(--royal);color:var(--white);padding:6px 6px;font-weight:600;margin-right:15px}
.slider{position:absolute;left:154px;top:154px;width:678px;height:297px;border-radius:10px;overflow:hidden;background:linear-gradient(160deg,#aeb8c2,#d9d5cf 35%,#8f7a63 60%,#6f7e52)}
.dots{position:absolute;left:10px;top:11px;display:flex;gap:3px}
.dots i{width:10px;height:3px;background:#ddd;display:block}
.dots i.on{background:var(--royal)}
.slide-band{position:absolute;left:0;bottom:0;width:678px;height:53px;background:rgba(20,20,20,.88)}
.slide-tab{position:absolute;left:0;bottom:40px;width:330px;height:36px;background:rgba(20,20,20,.88);border-radius:0 24px 0 0}
.welcome{position:absolute;left:15px;bottom:46px;color:var(--white);font:700 17px "Open Sans",sans-serif}
.intro{position:absolute;left:16px;bottom:19px;color:#eee;font-size:8.5px;line-height:11px;width:300px}
.quick{position:absolute;bottom:14px;display:flex;align-items:center;gap:6px;color:var(--white);font:500 8.5px "Montserrat",sans-serif;line-height:11px}
.quick .ico{width:24px;height:24px;display:flex;align-items:center;justify-content:center}
.quick .ico.blue{background:#3b8fe0;border-radius:3px}
.finder{position:absolute;left:626px;top:258px;width:178px;height:127px;background:var(--royal);box-shadow:0 0 0 1px rgba(255,255,255,.3)}
.finder-head{height:27px;background:linear-gradient(#f4f4f4,#dcdcdc);display:flex;align-items:center;gap:6px;padding-left:6px;font:600 10.5px "Montserrat",sans-serif;color:var(--royal);text-transform:uppercase}
.field{position:absolute;background:var(--white);border:1px solid #9aa6cf;font-size:8.5px;color:#444;height:17px;padding:2px 5px}
.finder-btn{position:absolute;left:11px;top:97px;width:88px;height:18px;background:linear-gradient(#fff,#dcdcdc);font:500 8.5px "Montserrat",sans-serif;color:var(--royal);display:flex;align-items:center;gap:4px;padding-left:6px}
.arrow{position:absolute;top:281px}
.divider{position:absolute;left:124px;width:730px;height:1px;background:#dedede}
.card{position:absolute;top:506px;width:146px}
.card-img{height:84px;border-radius:3px 3px 0 0;position:relative;overflow:hidden}
.card-label{position:absolute;left:0;bottom:0;width:100%;height:24px;background:var(--royal);color:var(--white);font:600 8.3px "Open Sans",sans-serif;padding:6px 6px;white-space:nowrap;letter-spacing:-.1px}
.card p{margin-top:14px;padding-left:7px;font-size:8px;line-height:12.3px;color:var(--muted)}
.sect-title{position:absolute;left:162px;top:681px;display:flex;align-items:center;gap:5px;font:500 11px "Montserrat",sans-serif;color:var(--royal);text-transform:uppercase}
.sect-title i{width:10px;height:10px;background:var(--royal);display:block}
.gallery{position:absolute;left:162px;top:701px;width:443px;height:144px;border:1px solid #ccc;background:var(--white)}
.gallery div{position:absolute}
.gallery-text{position:absolute;left:162px;top:860px;width:440px;font-size:8.5px;line-height:12.5px;color:#555}
.social-box{position:absolute;left:633px;top:698px;width:193px;height:64px;background:var(--royal);box-shadow:0 6px 6px -4px rgba(0,0,0,.25)}
.social-box .small{position:absolute;left:11px;top:9px;font-size:8.5px;color:#8fa0d8}
.social-box .name{position:absolute;left:11px;top:24px;font:700 19px "Open Sans",sans-serif;letter-spacing:-.4px;color:var(--white)}
.social-box .like{position:absolute;left:136px;top:23px;width:47px;height:15px;background:#eef0f7;font-size:7.5px;color:var(--royal);padding:2px 0 0 18px}
.assoc-box{position:absolute;left:633px;top:786px;width:193px;height:78px;background:var(--white);border:1px solid #d6d6d6;box-shadow:0 6px 6px -4px rgba(0,0,0,.2)}
.assoc-box h4{position:absolute;left:10px;top:9px;width:112px;font:600 10px "Open Sans",sans-serif;color:#333;line-height:13px}
.assoc-box a{position:absolute;left:13px;top:58px;font-size:8px;color:#333}
.assoc-box .seal{position:absolute;left:127px;top:8px;width:58px;height:58px;border-radius:50%;border:2px solid #b9bcc4;background:#eceef2}
.footer{position:absolute;left:120px;top:908px;width:738px;height:292px;background:var(--footer);border-top:4px solid #4a4a4a;color:#ccc}
.fcol{position:absolute;top:26px}
.fcol h3{font:500 11.5px "Montserrat",sans-serif;color:var(--white);text-transform:uppercase;margin-bottom:20px}
.news{display:flex;gap:10px;margin-bottom:10px}
.news .thumb{width:41px;height:41px;flex:none}
.news b{display:block;font:500 10px "Open Sans",sans-serif;color:var(--white);margin-top:1px}
.news span{display:block;font-size:7px;line-height:11px;color:#aaa;width:150px}
.tweet{font-size:8px;line-height:14px;color:#aaa;width:145px}
.tweet em{font-style:normal;color:#fff}
.when{display:flex;align-items:center;gap:6px;font-size:8px;color:#ddd;margin:12px 0 14px}
.popular li{list-style:none;font-size:8.5px;color:#ddd;margin-bottom:13px;display:flex;align-items:center;gap:8px}
.popular li:before{content:"";border-left:4px solid #ddd;border-top:3px solid transparent;border-bottom:3px solid transparent}
.fgrid{display:grid;grid-template-columns:repeat(3,44px);gap:6px 4px;margin-top:-3px}
.fgrid div{height:44px}
.copyright{position:absolute;left:41px;top:266px;font-size:8px;color:#bbb}
.copyright b{font-weight:400;color:#fff}
.footer-rule{position:absolute;left:0;top:250px;width:738px;height:1px;background:var(--footer-line)}
</style>
</head>
<body>
<div class="side-scene left" role="img" aria-label="House framing under construction seen through timber studs"></div>
<div class="side-scene right" role="img" aria-label="House framing under construction with houses in the distance"></div>
<div class="top-rule"></div>

<div class="sheet"></div>

<div class="social" aria-label="Social links"><span></span><span></span><span></span><span></span></div>
<div class="brand">PHOVAN</div>
<div class="contact">
  <div><span class="lab">Phone:</span>(800) 555-0142</div>
  <div><span class="lab"></span>(916) 555-0187</div>
  <div style="margin-top:6px"><span class="lab">Email:</span><a href="#">hello@phovan.org</a></div>
</div>

<ul class="nav">
  <li class="current">Home</li>
  <li>Find an Inspector</li>
  <li>Home Buyers &amp; Sellers</li>
  <li style="margin-right:22px">Real Estate Agents</li>
  <li style="margin-right:22px">Inspectors</li>
  <li>Ask PHOVAN</li>
  <li>Contact Us</li>
</ul>

<svg class="arrow" style="left:129px" width="12" height="26" viewBox="0 0 12 26"><path d="M10 1 2 13l8 12" fill="none" stroke="#777" stroke-width="1.5"/></svg>
<svg class="arrow" style="left:839px" width="12" height="26" viewBox="0 0 12 26"><path d="M2 1l8 12-8 12" fill="none" stroke="#777" stroke-width="1.5"/></svg>

<div class="slider" role="img" aria-label="Home inspectors taking notes in front of a brick suburban house">
  <div class="dots"><i></i><i></i><i></i><i class="on"></i></div>
  <div class="slide-tab"></div>
  <div class="slide-band"></div>
  <div class="welcome">Welcome to PHOVAN</div>
  <div class="intro">The Pacific Home Valuation &amp; Inspection Network (PHOVAN) is a voluntary, nonprofit public-benefit organization of real estate inspectors.</div>
  <div class="quick" style="left:368px">
    <span class="ico"><svg width="20" height="18" viewBox="0 0 20 18"><g fill="#fff"><rect y="0" width="20" height="2"/><rect y="4" width="20" height="2"/><rect y="8" width="20" height="2"/><rect y="12" width="20" height="2"/><rect y="16" width="20" height="2"/></g></svg></span>
    <span>INSPECTOR<br>LOGIN</span>
  </div>
  <div class="quick" style="left:467px">
    <span class="ico blue"><svg width="14" height="14" viewBox="0 0 14 14"><path d="M2 13V2h9l-2 3 2 3H3" fill="none" stroke="#fff" stroke-width="1.6"/></svg></span>
    <span>SEARCH FOR<br>INSPECTOR</span>
  </div>
  <div class="quick" style="left:586px">
    <span class="ico"><svg width="20" height="20" viewBox="0 0 20 20"><rect x="2" y="3" width="16" height="13" rx="3" fill="none" stroke="#fff" stroke-width="1.5"/><path d="M6 16l-2 3 5-3" fill="#fff"/><circle cx="7" cy="8" r="1" fill="#fff"/><circle cx="13" cy="8" r="1" fill="#fff"/><path d="M6 11q4 3 8 0" fill="none" stroke="#fff" stroke-width="1.3"/></svg></span>
    <span>UP COMMING<br>EVENTS</span>
  </div>
</div>

<div class="finder">
  <div class="finder-head">
    <svg width="20" height="18" viewBox="0 0 20 18"><rect x="1" y="2" width="13" height="14" rx="1" fill="none" stroke="#243a94" stroke-width="1.4"/><circle cx="12" cy="8" r="4" fill="#fff" stroke="#243a94" stroke-width="1.4"/><path d="M15 11l4 4" stroke="#243a94" stroke-width="1.8"/></svg>
    Search for Inspector
  </div>
  <div class="field" style="left:11px;top:39px;width:151px">Distance
    <svg style="position:absolute;right:6px;top:5px" width="8" height="5" viewBox="0 0 8 5"><path d="M0 0h8L4 5z" fill="#222"/></svg></div>
  <div class="field" style="left:11px;top:69px;width:73px">From
    <svg style="position:absolute;right:3px;top:3px" width="11" height="10" viewBox="0 0 11 10"><rect width="11" height="10" fill="#6b7fc4"/><rect x="1" y="3" width="9" height="6" fill="#fff"/></svg></div>
  <div class="field" style="left:88px;top:69px;width:74px">To
    <svg style="position:absolute;right:3px;top:3px" width="11" height="10" viewBox="0 0 11 10"><rect width="11" height="10" fill="#6b7fc4"/><rect x="1" y="3" width="9" height="6" fill="#fff"/></svg></div>
  <div class="finder-btn">
    <svg width="11" height="11" viewBox="0 0 11 11"><rect x="0.5" y="0.5" width="10" height="10" fill="none" stroke="#243a94"/><circle cx="5" cy="5" r="2.5" fill="none" stroke="#243a94"/><path d="M7 7l3 3" stroke="#243a94"/></svg>
    SEARCH NOW
  </div>
</div>

<div class="divider" style="top:478px"></div>

<div class="card" style="left:159px">
  <div class="card-img" role="img" aria-label="Forest path through green trees" style="background:linear-gradient(#3f6b2a,#6ea23b 60%,#8a7a4a)"><div class="card-label">Path to Success Program</div></div>
  <p>Duis aute irure dolor reprehenderit in voluptate velit esse cillum dolore eu fugiat nulla pariatur. Excepteur sint occaecat cupidatat.</p>
</div>
<div class="card" style="left:332px">
  <div class="card-img" role="img" aria-label="Raised hand in front of a green chalkboard" style="background:linear-gradient(90deg,#1f6a45,#3a8a5c 60%,#d9b89c 75%,#2a7450)"><div class="card-label">Educational Publications</div></div>
  <p>Lorem ipsum dolor sit consectetur adipisicing elit amet sid do eiusmod tempor incididunt labore sint occaecat.</p>
</div>
<div class="card" style="left:505px">
  <div class="card-img" role="img" aria-label="New construction specialist badge on white" style="background:#fff;border:1px solid #ddd;border-bottom:none">
    <div style="position:absolute;left:40px;top:14px;width:30px;height:30px;border-radius:50%;background:#d8d8d8"></div>
    <div class="card-label">PHOVAN New Construction</div></div>
  <p>Duis aute irure dolor reprehenderit in voluptate velit esse cillum dolore eu fugiat nulla pariatur. Excepteur sint occaecat cupidatat.</p>
</div>
<div class="card" style="left:678px">
  <div class="card-img" role="img" aria-label="Grey two-storey house facade" style="background:linear-gradient(#8e99a6,#5f6a76)"><div class="card-label">PHOVAN Press / Media Archives</div></div>
  <p>Duis aute irure dolor reprehenderit in voluptate velit esse cillum dolore eu fugiat nulla pariatur. Excepteur sint occaecat cupidatat.</p>
</div>

<div class="divider" style="top:672px;left:159px;width:670px;background:#e6e6e6"></div>

<div class="sect-title"><i></i>Gallery</div>
<div class="gallery">
  <div role="img" aria-label="Woman reading in a blue lounge chair" style="left:3px;top:3px;width:131px;height:69px;background:linear-gradient(#e4e8ec,#b9c3d4 70%,#3250a8)"></div>
  <div role="img" aria-label="Glass skylight roof" style="left:3px;top:74px;width:131px;height:66px;background:linear-gradient(135deg,#a7c6dc,#5a89a8 60%,#cfe0ea)"></div>
  <div role="img" aria-label="Man in suit looking out an office window over a city" style="left:137px;top:3px;width:167px;height:137px;background:linear-gradient(90deg,#5b6068,#c9d0d6 40%,#dfe4e8 70%,#6d737a)"></div>
  <div role="img" aria-label="Building facade with siding" style="left:307px;top:3px;width:133px;height:68px;background:repeating-linear-gradient(#9a9a9a 0 3px,#dcdcdc 3px 6px)"></div>
  <div role="img" aria-label="Woman working on a laptop in a waiting area" style="left:307px;top:74px;width:133px;height:66px;background:linear-gradient(#f1f1f1,#cfcfcf 70%,#3c3c3c)"></div>
</div>
<p class="gallery-text">El aluminio es un metal que se distingue de otros materiales por su propiedades tecnológicas. Su ligereza y su resistencia mecánica, lo hacen útil para múltiples y exigentes aplicaciones, ya que su densidad es un</p>

<div class="social-box">
  <div class="small">Pacific Home Valuation</div>
  <div class="name">Friendbook</div>
  <div class="like"><svg style="position:absolute;left:5px;top:3px" width="9" height="9" viewBox="0 0 9 9"><rect width="9" height="9" fill="#243a94"/></svg>Like</div>
</div>
<div class="assoc-box">
  <h4>Pacific Home Valuation &amp; Inspection Network</h4>
  <a href="#">Read More</a>
  <div class="seal"></div>
</div>

<div class="footer">
  <div class="fcol" style="left:41px">
    <h3>Latest News</h3>
    <div class="news"><div class="thumb" role="img" aria-label="People at a restaurant table" style="background:linear-gradient(135deg,#6b2a1e,#d89a7c,#3a2a28)"></div><div><b>Schedule</b><span>Lorem ipsum dolor amet laboris consectetur adipisicing elit,</span></div></div>
    <div class="news"><div class="thumb" role="img" aria-label="Couple outdoors" style="background:linear-gradient(135deg,#4d6b3a,#c9b49a,#5a6a4a)"></div><div><b>Confrence Schedule</b><span>Lorem ipsum dolor amet laboris consectetur adipisicing elit,</span></div></div>
    <div class="news"><div class="thumb" role="img" aria-label="Orange flowers" style="background:linear-gradient(135deg,#e87a1e,#f6c06a,#b5461a)"></div><div><b>General Information</b><span>Lorem ipsum dolor amet laboris consectetur adipisicing elit,</span></div></div>
  </div>
  <div class="fcol" style="left:258px">
    <h3 style="margin-bottom:18px">Latest Tweets</h3>
    <p class="tweet">Burgerly goes abstract with crowd-sourced animations: <em>http://go.ph/Ee0ZrviJp</em></p>
    <div class="when"><svg width="10" height="10" viewBox="0 0 10 10"><circle cx="5" cy="5" r="4" fill="none" stroke="#fff" stroke-width="1.3"/><path d="M5 2.5V5h2" fill="none" stroke="#fff"/></svg>34 mins ago</div>
    <p class="tweet">"Sheet to Site Import" useable especially for directory sitebuilder theme <em>http://go.ph/Ps7gVgDWJx #sitebuilder #plugin</em></p>
    <div class="when" style="margin-top:20px"><svg width="10" height="10" viewBox="0 0 10 10"><circle cx="5" cy="5" r="4" fill="none" stroke="#fff" stroke-width="1.3"/><path d="M5 2.5V5h2" fill="none" stroke="#fff"/></svg>1 hour ago</div>
    <div style="width:145px;height:1px;background:#444;margin-top:-4px"></div>
  </div>
  <div class="fcol" style="left:422px">
    <h3>Popular</h3>
    <ul class="popular">
      <li>Inspection FAQs</li><li>Common Venting of Gas</li><li>Becoming a Member</li><li>Education / CECs</li><li>Affiliate Directory</li><li>Lorem Lipsum</li>
    </ul>
  </div>
  <div class="fcol" style="left:559px">
    <h3>Gallery</h3>
    <div class="fgrid" role="img" aria-label="Nine small photos of concerts, lights and evening scenes">
      <div style="background:#2a3552"></div><div style="background:linear-gradient(90deg,#1c3fb8,#e6e6e6)"></div><div style="background:#2b1a16"></div>
      <div style="background:linear-gradient(#5a3a24,#c9924e)"></div><div style="background:radial-gradient(#e08a3a,#2a1a12)"></div><div style="background:linear-gradient(#7a6a3a,#3c3424)"></div>
      <div style="background:#3a2e22"></div><div style="background:#2a2422"></div><div style="background:#3a2c28"></div>
    </div>
  </div>
  <div class="footer-rule"></div>
  <div class="copyright">© 2012 Copyright by <b>Real Estate</b>&nbsp;&nbsp; All rights reserved.</div>
</div>
</body>
</html>
```